Construction business card

I need a new business card, they can connect with my logo, brand.
What we do is residential house , design and build
I like: Navy blue / black
I attached our logo, brand,
and, some idea for business card.

```html
<!DOCTYPE html>
<html lang="en">
<head>
<meta charset="utf-8">
<title>Ardent Building Group – Business Card</title>
<link href="https://fonts.googleapis.com/css2?family=Arimo:wght@400;700&display=swap" rel="stylesheet">
<style>
  :root {
    --backdrop: #1c1c1d;
    --card: #2b2b2c;
    --gloss: #151516;
    --accent: #3a86d0;
    --ink: #ffffff;
    --ink-soft: #e4e4e4;
  }
  * { box-sizing: border-box; margin: 0; padding: 0; }
  html, body {
    width: 1200px; height: 900px; overflow: hidden;
    background: var(--backdrop);
    font-family: "Arimo", Arial, sans-serif;
  }
  .stage {
    position: relative; width: 1200px; height: 900px;
    display: flex; flex-direction: column; align-items: center;
    justify-content: center; gap: 30px;
  }
  .card {
    width: 700px; height: 400px; border-radius: 22px;
    background: var(--card); position: relative;
  }
  /* front */
  .card--front { display: flex; align-items: center; justify-content: center; }
  .wordmark {
    display: flex; align-items: center; gap: 14px;
    font-weight: 700; text-transform: uppercase; letter-spacing: 2px;
  }
  .wordmark__square { width: 22px; height: 22px; }
  .card--front .wordmark { font-size: 40px; color: var(--gloss); }
  .card--front .wordmark__square { background: var(--gloss); }
  /* back */
  .card--back { display: flex; align-items: center; }
  .card__brand {
    width: 370px; display: flex; justify-content: center;
  }
  .card--back .wordmark { font-size: 24px; color: var(--ink); letter-spacing: 1.5px; }
  .card--back .wordmark__square { background: var(--accent); width: 18px; height: 18px; }
  .divider {
    width: 1.5px; height: 190px; background: var(--accent);
  }
  .card__details { padding-left: 40px; color: var(--ink-soft); }
  .person__name {
    color: var(--accent); font-weight: 700; font-size: 25px;
    text-transform: uppercase; letter-spacing: 0.5px;
  }
  .person__role { font-size: 15px; margin-top: 3px; }
  .address { font-size: 15px; line-height: 1.35; margin-top: 20px; font-style: normal; }
  .contacts { list-style: none; margin-top: 18px; font-size: 15px; }
  .contacts li { display: flex; align-items: center; gap: 9px; line-height: 1.6; }
  .contacts svg { width: 12px; height: 12px; flex: none; }
</style>
</head>
<body>
<main class="stage">
  <section class="card card--front" aria-label="Card front">
    <div class="wordmark"><span class="wordmark__square"></span>Ardent Building Group</div>
  </section>

  <section class="card card--back" aria-label="Card back">
    <div class="card__brand">
      <div class="wordmark"><span class="wordmark__square"></span>Ardent Building Group</div>
    </div>
    <div class="divider"></div>
    <div class="card__details">
      <h1 class="person__name">Daniel Harper</h1>
      <p class="person__role">CEO/Founder</p>
      <address class="address">48 Ridgeview Rd,<br>Elmstone, VIC 3190</address>
      <ul class="contacts">
        <li>
          <svg viewBox="0 0 12 12" fill="#dcdcdc" aria-hidden="true"><path d="M2.5 0.8 4.3 2.8 3.3 4.2C3.9 5.6 6.4 8.1 7.8 8.7L9.2 7.7 11.2 9.5 10 11.2C5.6 11 1 6.4 0.8 2Z"/></svg>
          0400 555 018
        </li>
        <li>
          <svg viewBox="0 0 12 12" aria-hidden="true"><rect x="0.5" y="2" width="11" height="8" rx="1" fill="#dcdcdc"/><path d="M0.8 2.4 6 6.6 11.2 2.4" fill="none" stroke="#2b2b2c" stroke-width="1"/></svg>
          info@ardentbuildinggroup.com.au
        </li>
        <li>
          <svg viewBox="0 0 12 12" fill="none" stroke="#dcdcdc" stroke-width="1" aria-hidden="true"><circle cx="6" cy="6" r="5"/><ellipse cx="6" cy="6" rx="2.2" ry="5"/><path d="M1 6H11"/></svg>
          ardentbuildinggroup.com.au
        </li>
      </ul>
    </div>
  </section>
</main>
</body>
</html>
```